Online business manager needs a website

I need a website designed and then coded. I am an online business manager serving a number of different industries providing administrative support to existing small businesses and helping solo practitioners get their new business up and running.

I didn't have a logo formally designed but have been using the attached avatar and wouldn't mind something that incorporated that.

The business doesn't have an official name, so I've just been using my name Lena Morvath, Online Business Manager or Lena Morvath, OBM. I've attached two documents that I have made previously for an example of content.

I would prefer the final site be in Wordpress.

Requirements
Must have
• A way to contact me, testimonials, list of services

```html
<!DOCTYPE html>
<html lang="en">
<head>
<meta charset="utf-8">
<title>Lena Morvath – Online Business Manager – Website Options</title>
<link rel="stylesheet" href="https://fonts.googleapis.com/css2?family=Poppins:wght@300;400;500;600;700&family=Montserrat:wght@700&display=swap">
<style>
:root{
  --ink:#1d1d2b;
  --muted:#6d6d7d;
  --line:#e7e7ee;
  --paper:#ffffff;
  --mist:#f4f4f7;
  --lilac:#e9e2fb;
  --purple:#5c20ad;
  --purple-deep:#3b0f7a;
  --purple-dark:#2c0a5e;
  --violet:#7b35d6;
  --green:#1ec97c;
  --teal:#0f8f8e;
  --teal-dark:#0a7a87;
  --cyan:#1dc4e8;
  --navy:#1b2a9e;
  --navy-deep:#0d1766;
  --gold:#ffd21c;
  --orange:#f7931e;
  --black:#050507;
}
*{box-sizing:border-box;margin:0;padding:0}
html,body{width:1200px;height:2640px;overflow:hidden;background:var(--paper)}
body{position:relative;font-family:"Poppins",sans-serif;color:var(--ink)}
.abs{position:absolute}
.option-title{position:absolute;top:72px;font-family:"Montserrat",sans-serif;font-weight:700;font-size:38px;letter-spacing:1px;color:var(--black);width:400px;text-align:center}
.site{position:absolute;top:156px;height:2394px;overflow:hidden;background:var(--paper);box-shadow:0 4px 22px rgba(0,0,0,.12)}
.site-1{left:53px;width:505px}
.site-2{left:600px;width:543px}

/* nav */
.nav{position:absolute;top:0;left:0;right:0;height:40px;display:flex;align-items:center;padding:0 28px;justify-content:space-between}
.brand{display:flex;align-items:center;gap:6px;font-size:10px;font-weight:500}
.brand-mark{width:20px;height:20px;border-radius:3px;background:var(--orange)}
.nav-links{display:flex;gap:17px;font-size:5.5px;font-weight:500;letter-spacing:.2px}
.nav-links .on{color:var(--violet)}
.nav-dark .brand,.nav-dark .nav-links{color:#fff}
.nav-dark .nav-links .on{color:var(--orange)}

/* hero */
.hero-head{font-size:23px;line-height:31px;font-weight:300}
.hero-head b{font-weight:500}
.hero-text{font-size:5.5px;line-height:9px;color:var(--muted)}
.btn{position:absolute;height:19px;padding:0 14px;background:#fff;border:1px solid var(--purple-dark);font-size:5.5px;font-weight:600;display:flex;align-items:center;box-shadow:-4px 4px 0 var(--purple)}
.btn-cyan{box-shadow:-4px 4px 0 var(--cyan);border-color:#fff}
.photo{position:absolute;background:linear-gradient(135deg,#c43a7c,#3a3640 60%,#d9c9b8)}
.photo-soft{background:linear-gradient(135deg,#8a7a66,#cfb9a2 55%,#6b6f7a)}

/* headings */
.kicker{position:absolute;left:0;right:0;text-align:center;font-size:5.5px;letter-spacing:.3px;text-transform:uppercase}
.sec-title{position:absolute;left:0;right:0;text-align:center;font-size:14px;font-weight:500}
.light{color:#fff}
.kicker-left{font-size:5.5px;text-transform:uppercase}
.title-left{font-size:14px;font-weight:500;margin:3px 0 12px}
.body-text{font-size:5.6px;line-height:9.6px;color:var(--muted)}

/* skills */
.skill-card{position:absolute;background:#fff;border-radius:5px;box-shadow:0 2px 10px rgba(0,0,0,.1);padding:8px 12px}
.skill-card.feature{background:linear-gradient(180deg,var(--violet),var(--purple-deep));color:#fff}
.skill-card li{list-style:none;font-size:5.6px;border-bottom:1px solid var(--line);padding:5.5px 0 5.5px 4px;position:relative}
.skill-card.feature li{border-color:rgba(255,255,255,.2)}
.skill-card li::before{content:"";position:absolute;left:0;top:8.5px;width:2px;height:2px;border-radius:50%;background:var(--violet)}
.skill-card.feature li::before{background:#fff}

/* services */
.svc{position:absolute;color:#fff}
.svc-green{background:var(--green)}
.svc-teal{background:var(--teal)}
.svc-deep{background:var(--teal-dark)}
.svc h3{font-size:8.5px;font-weight:500;margin-bottom:6px}
.svc li{list-style:none;font-size:5px;line-height:12.5px}
.svc li::before{content:"• "}
.svc-icon{width:26px;height:26px;border:1.5px solid #fff;border-radius:5px;margin-bottom:10px}
.svc-img{position:absolute;left:0;top:0;right:0;height:85px;background:linear-gradient(135deg,#dfe3e8,#9aa4ae)}
.arrow-thin{position:absolute;font-size:14px;color:var(--muted);font-weight:300}

/* portfolio */
.tile{position:absolute}
.t1{background:linear-gradient(135deg,#f2f2f2,#cfd3d8)}
.t2{background:linear-gradient(135deg,#4f2a95,#3a1a78)}
.t3{background:linear-gradient(135deg,#2e2e32,#1a1a1d)}
.t4{background:linear-gradient(135deg,#3c2b4a,#c96b4a 60%,#2b2240)}
.t5{background:linear-gradient(135deg,#8a3d1e,#c26a3a)}
.t6{background:linear-gradient(135deg,#d7dde2,#b2804e)}

/* blog */
.blog-img{position:absolute;height:95px;border-radius:4px 4px 0 0;background:linear-gradient(135deg,#cfd6dc,#6c7580)}
.date-badge{position:absolute;left:6px;top:5px;width:16px;height:16px;border-radius:50%;background:var(--purple);color:#fff;font-size:3.6px;text-align:center;line-height:5px;padding-top:3px}
.blog-title{position:absolute;font-size:7px;font-weight:500;line-height:10.5px}
.blog-text{position:absolute;font-size:5px;color:var(--muted)}

/* pricing */
.pricing-band{position:absolute;left:0;right:0;background:radial-gradient(ellipse at 30% 20%,#6a2bc0,var(--purple) 45%,var(--purple-deep))}
.plan{position:absolute;width:102px;height:140px}
.plan-back{position:absolute;left:0;top:26px;width:102px;height:90px;background:var(--purple-dark);clip-path:polygon(50% 0,100% 35%,100% 100%,0 100%,0 35%)}
.plan-card{position:absolute;left:20px;top:52px;width:64px;height:78px;background:#fff;clip-path:polygon(0 0,100% 0,100% 88%,0 100%);font-size:5.4px;line-height:9px;text-align:center;padding:22px 6px 0;color:var(--ink)}
.plan-pill{position:absolute;left:12px;top:44px;height:9px;padding:0 10px;border-radius:5px;background:var(--violet);color:#fff;font-size:4.4px;font-weight:600;line-height:9px;text-transform:uppercase}
.plan-hex{position:absolute;left:33px;top:0;width:36px;height:40px;background:#fff;clip-path:polygon(50% 0,100% 25%,100% 75%,50% 100%,0 75%,0 25%)}
.plan-hex span{position:absolute;inset:2px;background:var(--purple-dark);clip-path:polygon(50% 0,100% 25%,100% 75%,50% 100%,0 75%,0 25%);color:#fff;font-size:8px;font-weight:500;display:flex;align-items:center;justify-content:center}

/* testimonials */
.avatar{position:absolute;border-radius:50%;background:linear-gradient(135deg,#caa58a,#6e5a52)}
.quote-photo{position:absolute;background:linear-gradient(135deg,#e7c27a,#b04d5a)}
.dot{position:absolute;border-radius:50%}
.stars{position:absolute;left:0;right:0;text-align:center;color:var(--orange);font-size:7px;letter-spacing:3px}
.quote{position:absolute;text-align:center;font-size:6.3px;line-height:11.5px;color:var(--muted)}
.circle-arrow{position:absolute;width:22px;height:22px;border-radius:50%;background:#eef0f8;font-size:12px;display:flex;align-items:center;justify-content:center;color:var(--ink)}

/* footer */
.footer{position:absolute;left:0;right:0;bottom:0;background:var(--black);color:#fff}
.foot-col h4{font-size:5.6px;font-weight:600;margin-bottom:8px}
.foot-col li{list-style:none;font-size:5px;line-height:14px;color:#cfcfd6}
.social{display:flex;gap:6px}
.social span{width:13px;height:13px;border-radius:50%;background:#2a2a33}
.social span:first-child{background:var(--purple)}
.contact-row{display:flex;gap:8px;align-items:center;font-size:5px;line-height:7px;color:#cfcfd6;margin-bottom:12px}
.contact-row i{flex:none;width:16px;height:16px;border-radius:50%;border:1px solid #fff;display:flex;align-items:center;justify-content:center}
.copyright{position:absolute;left:0;right:0;text-align:center;font-size:4.8px;color:#cfcfd6}
.copyright b{color:var(--violet);font-weight:400}
.signature{position:absolute;height:16px;border-radius:8px;background:#eeeaf6}
</style>
</head>
<body>

<h1 class="option-title" style="left:105px">OPTION 1</h1>
<h1 class="option-title" style="left:672px">OPTION 2</h1>

<!-- ================= OPTION 1 ================= -->
<section class="site site-1" aria-label="Website option one">
  <div class="abs" style="left:0;top:0;width:505px;height:318px;background:var(--mist)"></div>
  <svg class="abs" style="left:0;top:250px" width="505" height="70" viewBox="0 0 505 70"><path d="M0 40 C120 10 200 60 300 40 C390 22 450 20 505 30 L505 70 L0 70Z" fill="#ebebf0"/><path d="M0 55 C120 30 220 75 320 55 C400 40 460 42 505 48 L505 70 L0 70Z" fill="#fff"/></svg>
  <nav class="nav">
    <div class="brand"><span class="brand-mark"></span>Lena Morvath</div>
    <div class="nav-links"><span class="on">HOME</span><span>ABOUT LENA</span><span>SERVICES</span><span>PORTFOLIO</span><span>PRICING</span><span>CONTACT US</span></div>
  </nav>
  <div class="photo" role="img" aria-label="Portrait of Lena Morvath in front of pink flowers" style="left:28px;top:58px;width:198px;height:228px;border-radius:4px 60% 30% 4px / 4px 45% 40% 4px"></div>
  <div class="abs" style="left:384px;top:100px;width:34px;height:34px;border-radius:50%;background:var(--purple-deep)"></div>
  <h2 class="abs hero-head" style="left:300px;top:72px">Better<br><b>Communication</b><br>For Marketing</h2>
  <p class="abs hero-text" style="left:300px;top:170px;width:175px">Sed ut perspiciatis unde omnis iste natus error sit voluptatem accusantium doloremque laudantium</p>
  <a class="btn" style="left:304px;top:206px">READ MORE</a>
  <div class="abs" style="left:378px;top:210px;width:12px;height:12px;border-radius:50%;background:var(--purple-deep);color:#fff;font-size:6px;text-align:center;line-height:12px">›</div>
  <span class="abs" style="left:391px;top:212px;font-size:5px;color:var(--purple)">Chat</span>

  <div class="abs" style="left:28px;top:376px;width:200px">
    <div class="kicker-left">Welcome to</div>
    <h2 class="title-left">Online Business Manager</h2>
    <p class="body-text">Hi! I'm so excited that you have chosen to explore my portfolio. Helping businesses achieve their goals is my passion, and I'm thrilled that with my assistance you will have more time for your own passion project. I thrive while working independently, which means you can be confident when leaving tasks for me.</p>
  </div>
  <a class="btn" style="left:32px;top:486px">READ MORE</a>
  <div class="abs" style="left:260px;top:350px;width:100px;height:100px;border-radius:10px 0 0 0;background:var(--purple-deep)"></div>
  <div class="abs" style="left:330px;top:352px;width:140px;height:136px;border:1px solid #aaa;border-radius:0 6px 16px 0"></div>
  <div class="photo photo-soft" role="img" aria-label="Smiling portrait of Lena outdoors" style="left:278px;top:362px;width:182px;height:163px;border-radius:30px 0 0 0"></div>
  <div class="signature" role="img" aria-label="Handwritten signature" style="left:266px;top:500px;width:80px"></div>

  <h2 class="sec-title" style="top:555px">What Our Skills</h2>
  <ul class="skill-card" style="left:28px;top:583px;width:137px;height:166px"><li>Office Suite</li><li>Design Studio</li><li>Social Pages</li><li>Task Boards</li><li>Post Scheduler</li><li>Ledger Books</li><li>Mail Campaigns</li><li>Video Calls</li></ul>
  <ul class="skill-card feature" style="left:184px;top:583px;width:137px;height:166px"><li>Cloud Docs</li><li>Basic Photo Editing</li><li>Photo Feeds</li><li>Kanban Boards</li><li>Feed Planner</li><li>Invoice Tools</li><li>A/P &amp; A/R</li><li>Note Keeping</li></ul>
  <ul class="skill-card" style="left:340px;top:583px;width:137px;height:166px"><li>Web Meetings</li><li>HR Portal</li><li>Audio Editing</li><li>Transcripts</li><li>Contact CRM</li><li>Cloud Accounting</li><li>Communication</li><li>Attention to detail</li></ul>

  <div class="abs" style="left:0;top:790px;width:505px;height:235px;background:var(--mist)"></div>
  <div class="kicker" style="top:822px">Services</div>
  <h2 class="sec-title" style="top:830px">What We Do</h2>
  <span class="arrow-thin" style="left:9px;top:914px">‹</span>
  <span class="arrow-thin" style="left:488px;top:914px">›</span>
  <div class="svc svc-green" style="left:28px;top:860px;width:140px;height:136px;padding:14px 8px"><div class="svc-icon"></div><h3>Virtual Assistance</h3><ul><li>Calendar Management</li><li>Email Management</li><li>Light Graphic Design</li><li>Data Entry</li></ul></div>
  <div class="svc svc-teal" style="left:181px;top:860px;width:140px;height:136px;padding:14px 8px"><div class="svc-icon"></div><h3>Finance Management</h3><ul><li>Create Invoices</li><li>Track Receivables</li><li>Analyze Expenses</li><li>Year Over Year Analytics</li></ul></div>
  <div class="svc svc-deep" style="left:334px;top:860px;width:140px;height:136px;padding:14px 8px"><div class="svc-icon"></div><h3>Business Management</h3><ul><li>Creation of Operating Procedures</li><li>Review of Website Strategy</li><li>Reporting and Analytics</li><li>Project Management</li></ul></div>

  <div class="kicker" style="top:1085px">Work</div>
  <h2 class="sec-title" style="top:1093px">My Portfolio</h2>
  <div class="tile t1" role="img" aria-label="Notebook sketch of a creative process" style="left:28px;top:1126px;width:146px;height:104px"></div>
  <div class="tile t2" role="img" aria-label="Purple gallery overlay" style="left:181px;top:1126px;width:146px;height:104px"></div>
  <div class="tile t3" role="img" aria-label="Desk with keyboard and coffee cup" style="left:333px;top:1126px;width:146px;height:104px"></div>
  <div class="tile t4" role="img" aria-label="Coloured pencils in a mug" style="left:28px;top:1236px;width:146px;height:104px"></div>
  <div class="tile t5" role="img" aria-label="Hands opening a leather bag" style="left:181px;top:1236px;width:146px;height:104px"></div>
  <div class="tile t6" role="img" aria-label="Travel journal with paper plane" style="left:333px;top:1236px;width:146px;height:104px"></div>

  <div class="kicker" style="top:1377px">Article</div>
  <h2 class="sec-title" style="top:1385px">Recent Blog</h2>
  <div class="blog-img" role="img" aria-label="Man working on a laptop" style="left:28px;top:1419px;width:142px"><span class="date-badge">12<br>June</span></div>
  <div class="blog-img" role="img" aria-label="Team in a bright office" style="left:181px;top:1419px;width:142px"><span class="date-badge">12<br>June</span></div>
  <div class="blog-img" role="img" aria-label="Woman reading at a cafe" style="left:333px;top:1419px;width:142px"><span class="date-badge">12<br>June</span></div>
  <p class="blog-title" style="left:28px;top:1520px;width:140px">Excepteur sint occaecat cupidatat non proident</p>
  <p class="blog-title" style="left:181px;top:1520px;width:140px">Excepteur sint occaecat cupidatat non proident</p>
  <p class="blog-title" style="left:333px;top:1520px;width:140px">Excepteur sint occaecat cupidatat non proident</p>
  <p class="blog-text" style="left:28px;top:1548px">Sed ut perspiciatis unde omnis iste natus...</p>
  <p class="blog-text" style="left:181px;top:1548px">Sed ut perspiciatis unde omnis iste natus...</p>
  <p class="blog-text" style="left:333px;top:1548px">Sed ut perspiciatis unde omnis iste natus...</p>
  <a class="btn" style="left:32px;top:1566px">READ MORE</a>
  <a class="btn" style="left:185px;top:1566px">READ MORE</a>
  <a class="btn" style="left:337px;top:1566px">READ MORE</a>

  <div class="pricing-band" style="top:1622px;height:250px"></div>
  <div class="kicker light" style="top:1655px">Our Pricing</div>
  <h2 class="sec-title light" style="top:1663px">Rated &amp; Packages</h2>
  <div class="plan" style="left:31px;top:1702px"><div class="plan-back"></div><div class="plan-card">For clients needing only occasional help</div><div class="plan-pill">Hourly rate</div><div class="plan-hex"><span>$40</span></div></div>
  <div class="plan" style="left:143px;top:1702px"><div class="plan-back"></div><div class="plan-card">Includes one 15 minute meeting per week</div><div class="plan-pill">20 hours/month</div><div class="plan-hex"><span>$700</span></div></div>
  <div class="plan" style="left:255px;top:1702px"><div class="plan-back"></div><div class="plan-card">Includes one 30 minute meeting per week</div><div class="plan-pill">40 hours/month</div><div class="plan-hex"><span>$1,300</span></div></div>
  <div class="plan" style="left:367px;top:1702px"><div class="plan-back"></div><div class="plan-card">Includes one 60 minute meeting per week</div><div class="plan-pill">80 hours/month</div><div class="plan-hex"><span>$2,400</span></div></div>

  <div class="kicker" style="top:1913px">Testimonials</div>
  <h2 class="sec-title" style="top:1921px">What Our Client Says</h2>
  <p class="abs" style="left:0;right:0;top:1950px;text-align:center;font-size:6px">Sed ut perspiciatis unde omnis iste natus error sit voluptatem accusantium</p>
  <div class="avatar" role="img" aria-label="Client photo" style="left:452px;top:1960px;width:20px;height:20px"></div>
  <div class="avatar" role="img" aria-label="Client photo" style="left:28px;top:2019px;width:30px;height:30px"></div>
  <svg class="abs" style="left:150px;top:2030px" width="210" height="40" viewBox="0 0 210 40"><path d="M2 36 C50 15 110 10 206 12" stroke="var(--cyan)" stroke-width="1.6" fill="none"/></svg>
  <div class="quote-photo" role="img" aria-label="Portrait of Marisa T. Owner" style="left:220px;top:1992px;width:55px;height:60px"></div>
  <span class="dot" style="left:60px;top:2007px;width:3px;height:3px;background:var(--cyan)"></span>
  <span class="dot" style="left:432px;top:2016px;width:5px;height:5px;background:var(--orange)"></span>
  <span class="dot" style="left:158px;top:2070px;width:5px;height:5px;background:var(--orange)"></span>
  <span class="dot" style="left:372px;top:2062px;width:3px;height:3px;background:var(--violet)"></span>
  <span class="dot" style="left:115px;top:2172px;width:3px;height:3px;background:var(--navy)"></span>
  <p class="abs" style="left:0;right:0;top:2056px;text-align:center;font-size:8px;font-weight:500">Marisa T. Owner</p>
  <p class="abs" style="left:0;right:0;top:2068px;text-align:center;font-size:5px;color:var(--muted)">Summit Home Works</p>
  <div class="stars" style="top:2078px">★★★★★</div>
  <div class="circle-arrow" style="left:28px;top:2083px">←</div>
  <div class="circle-arrow" style="left:444px;top:2083px">→</div>
  <p class="quote" style="left:95px;width:315px;top:2110px">When it became apparent that a project would take more time than I had, Lena stepped up to take on the required research. She was thorough and timely; able to meet a last-minute 12-hour deadline. I would highly recommend Lena to assist with your next project.</p>

  <footer class="footer" style="height:206px">
    <div class="abs" style="left:28px;top:36px;width:115px">
      <div class="brand" style="font-size:6.5px;color:#fff"><span class="brand-mark"></span>Lena Morvath</div>
      <p style="font-size:4.8px;line-height:8px;color:#cfcfd6;margin:10px 0 20px">Sed ut perspiciatis unde omnis iste natus error sit voluptatem...</p>
      <div class="social"><span></span><span></span><span></span></div>
    </div>
    <div class="abs foot-col" style="left:178px;top:30px"><h4>QUICK LINKS</h4><ul><li>Home</li><li>About Lena</li><li>Services</li><li>Portfolio</li><li>Pricing</li><li>Contact Us</li></ul></div>
    <div class="abs foot-col" style="left:267px;top:30px"><h4>SERVICES</h4><ul><li>Corporate Solution</li><li>Call Center Solution</li><li>Cloud System Solution</li></ul></div>
    <div class="abs foot-col" style="left:366px;top:30px;width:120px"><h4>CONTACT US</h4>
      <div class="contact-row"><i><svg width="7" height="8" viewBox="0 0 7 8"><path d="M3.5 8 C1 5 0.5 4 0.5 3 A3 3 0 0 1 6.5 3 C6.5 4 6 5 3.5 8Z" fill="#fff"/></svg></i><span>14/2k Lorem ipsum dolar sit amet Glassglow 25kl USA</span></div>
      <div class="contact-row"><i><svg width="7" height="7" viewBox="0 0 7 7"><path d="M1 0.5 L2.5 0.5 L3 2 L2 2.8 C2.5 3.8 3.2 4.5 4.2 5 L5 4 L6.5 4.5 L6.5 6 C3.5 6 1 3.5 1 0.5Z" fill="#fff"/></svg></i><span>555.014.2288</span></div>
      <div class="contact-row"><i><svg width="8" height="6" viewBox="0 0 8 6"><rect x=".5" y=".5" width="7" height="5" fill="none" stroke="#fff"/><path d="M.5 .5 L4 3.5 L7.5 .5" fill="none" stroke="#fff"/></svg></i><span>hello@lenamorvath.test</span></div>
    </div>
    <p class="copyright" style="top:172px">COPYRIGHT © 2023 <b>LENA MORVATH</b> . ALL RIGHTS RESERVED.</p>
  </footer>
</section>

<!-- ================= OPTION 2 ================= -->
<section class="site site-2" aria-label="Website option two">
  <div class="abs" style="left:0;top:0;width:543px;height:330px;background:radial-gradient(ellipse at 40% 30%,#2f42c8,var(--navy) 45%,var(--navy-deep))"></div>
  <svg class="abs" style="left:0;top:250px" width="543" height="110" viewBox="0 0 543 110"><path d="M0 48 C70 40 120 20 190 35 C260 50 300 80 380 60 C450 42 500 25 543 20 L543 110 L0 110Z" fill="var(--lilac)"/><path d="M0 62 C80 52 130 36 200 52 C270 68 310 92 390 72 C460 55 510 42 543 38 L543 110 L0 110Z" fill="#fff"/></svg>
  <nav class="nav nav-dark">
    <div class="brand"><span class="brand-mark"></span>Lena Morvath</div>
    <div class="nav-links"><span class="on">HOME</span><span>ABOUT LENA</span><span>SERVICES</span><span>PORTFOLIO</span><span>PRICING</span><span>CONTACT US</span></div>
  </nav>
  <h2 class="abs hero-head" style="left:30px;top:78px;color:#fff;font-size:25px;line-height:34px">Better<br><b>Commu<span style="color:var(--gold)">nica</span>tion</b><br>For Marketing</h2>
  <p class="abs hero-text" style="left:30px;top:190px;width:190px;color:#d9dcf5">Sed ut perspiciatis unde omnis iste natus error sit voluptatem accusantium doloremque laudantium</p>
  <a class="btn btn-cyan" style="left:38px;top:222px">READ MORE</a>
  <div class="abs" style="left:312px;top:62px;width:190px;height:272px;border-radius:95px;background:#fff"></div>
  <div class="photo" role="img" aria-label="Portrait of Lena Morvath in front of pink flowers" style="left:318px;top:68px;width:178px;height:260px;border-radius:89px"></div>
  <div class="abs" style="left:403px;top:336px;width:10px;height:10px;border-radius:50%;background:var(--purple);border:2px solid #fff"></div>

  <div class="photo photo-soft" role="img" aria-label="Smiling portrait of Lena outdoors" style="left:30px;top:387px;width:202px;height:188px;box-shadow:2px 2px 0 #222"></div>
  <div class="abs" style="left:296px;top:416px;width:215px">
    <div class="kicker-left">Welcome to</div>
    <h2 class="title-left">Online Business Manager</h2>
    <p class="body-text">Hi! I'm so excited that you have chosen to explore my portfolio. Helping businesses achieve their goals is my passion, and I'm thrilled that with my assistance you will have more time for your own passion project. I thrive while working independently, which means you can be confident when leaving tasks for me.</p>
  </div>
  <a class="btn btn-cyan" style="left:304px;top:532px;border-color:var(--ink)">READ MORE</a>
  <div class="signature" role="img" aria-label="Handwritten signature" style="left:385px;top:530px;width:85px"></div>

  <h2 class="sec-title" style="top:597px">What Our Skills</h2>
  <ul class="skill-card" style="left:30px;top:627px;width:150px;height:180px"><li>Office Suite</li><li>Design Studio</li><li>Social Pages</li><li>Task Boards</li><li>Post Scheduler</li><li>Ledger Books</li><li>Mail Campaigns</li><li>Video Calls</li></ul>
  <ul class="skill-card feature" style="left:196px;top:627px;width:150px;height:180px"><li>Cloud Docs</li><li>Basic Photo Editing</li><li>Photo Feeds</li><li>Kanban Boards</li><li>Feed Planner</li><li>Invoice Tools</li><li>A/P &amp; A/R</li><li>Note Keeping</li></ul>
  <ul class="skill-card" style="left:362px;top:627px;width:150px;height:180px"><li>Web Meetings</li><li>HR Portal</li><li>Audio Editing</li><li>Transcripts</li><li>Contact CRM</li><li>Cloud Accounting</li><li>Communication</li><li>Attention to detail</li></ul>

  <svg class="abs" style="left:0;top:845px" width="543" height="40" viewBox="0 0 543 40"><path d="M0 20 C120 40 260 -5 400 10 C470 18 510 14 543 8 L543 40 L0 40Z" fill="var(--purple-deep)"/></svg>
  <div class="abs" style="left:0;top:875px;width:543px;height:330px;background:linear-gradient(180deg,var(--purple-deep),#4a1694)"></div>
  <div class="kicker light" style="top:918px">Services</div>
  <h2 class="sec-title light" style="top:926px">What We Do</h2>
  <span class="arrow-thin" style="left:10px;top:1050px;color:#fff">‹</span>
  <span class="arrow-thin" style="left:524px;top:1050px;color:#fff">›</span>
  <div class="svc svc-green" style="left:30px;top:962px;width:152px;height:198px"><div class="svc-img" role="img" aria-label="Laptop on a desk"></div><div style="padding:107px 8px 0"><h3>Virtual Assistance</h3><ul><li>Calendar Management</li><li>Email Management</li><li>Light Graphic Design</li><li>Data Entry</li></ul></div></div>
  <div class="svc svc-teal" style="left:195px;top:962px;width:152px;height:198px"><div class="svc-img" role="img" aria-label="Calculator and invoices on a desk"></div><div style="padding:107px 8px 0"><h3>Finance Management</h3><ul><li>Create Invoices</li><li>Track Receivables</li><li>Analyze Expenses</li><li>Year Over Year Analytics</li></ul></div></div>
  <div class="svc svc-deep" style="left:360px;top:962px;width:152px;height:198px"><div class="svc-img" role="img" aria-label="Manager at a desk with sticky notes"></div><div style="padding:107px 8px 0"><h3>Business Management</h3><ul><li>Creation of Operating Procedures</li><li>Review of Website Strategy</li><li>Reporting and Analytics</li><li>Project Management</li></ul></div></div>

  <div class="kicker" style="top:1247px">Work</div>
  <h2 class="sec-title" style="top:1255px">My Portfolio</h2>
  <div class="tile t1" role="img" aria-label="Notebook sketch of a creative process" style="left:30px;top:1291px;width:158px;height:112px"></div>
  <div class="tile t2" role="img" aria-label="Purple gallery overlay" style="left:193px;top:1291px;width:158px;height:112px"></div>
  <div class="tile t3" role="img" aria-label="Desk with keyboard and coffee cup" style="left:356px;top:1291px;width:158px;height:112px"></div>
  <div class="tile t4" role="img" aria-label="Coloured pencils in a mug" style="left:30px;top:1409px;width:158px;height:112px"></div>
  <div class="tile t5" role="img" aria-label="Hands opening a leather bag" style="left:193px;top:1409px;width:158px;height:112px"></div>
  <div class="tile t6" role="img" aria-label="Travel journal with paper plane" style="left:356px;top:1409px;width:158px;height:112px"></div>

  <div class="pricing-band" style="top:1567px;height:240px"></div>
  <svg class="abs" style="left:0;top:1770px" width="543" height="70" viewBox="0 0 543 70"><path d="M0 30 C100 25 170 5 260 25 C350 45 420 60 543 40 L543 70 L0 70Z" fill="#fff"/><path d="M0 0 L543 0 L543 40 C420 60 350 45 260 25 C170 5 100 25 0 30Z" fill="#4d189a"/></svg>
  <div class="kicker light" style="top:1608px">Our Pricing</div>
  <h2 class="sec-title light" style="top:1616px">Rated &amp; Packages</h2>
  <div class="plan" style="left:38px;top:1655px"><div class="plan-back"></div><div class="plan-card">For clients needing only occasional help</div><div class="plan-pill">Hourly rate</div><div class="plan-hex"><span>$40</span></div></div>
  <div class="plan" style="left:161px;top:1655px"><div class="plan-back"></div><div class="plan-card">Includes one 15 minute meeting per week</div><div class="plan-pill">20 hours/month</div><div class="plan-hex"><span>$700</span></div></div>
  <div class="plan" style="left:282px;top:1655px"><div class="plan-back"></div><div class="plan-card">Includes one 30 minute meeting per week</div><div class="plan-pill">40 hours/month</div><div class="plan-hex"><span>$1,300</span></div></div>
  <div class="plan" style="left:403px;top:1655px"><div class="plan-back"></div><div class="plan-card">Includes one 60 minute meeting per week</div><div class="plan-pill">80 hours/month</div><div class="plan-hex"><span>$2,400</span></div></div>

  <div class="kicker" style="top:1882px">Testimonials</div>
  <h2 class="sec-title" style="top:1890px">What Our Client Says</h2>
  <p class="abs" style="left:0;right:0;top:1920px;text-align:center;font-size:6.3px">Sed ut perspiciatis unde omnis iste natus error sit voluptatem accusantium</p>
  <div class="avatar" role="img" aria-label="Client photo" style="left:490px;top:1926px;width:22px;height:22px"></div>
  <div class="avatar" role="img" aria-label="Client photo" style="left:32px;top:1991px;width:32px;height:32px"></div>
  <svg class="abs" style="left:160px;top:2010px" width="220" height="40" viewBox="0 0 220 40"><path d="M2 36 C50 14 120 10 216 10" stroke="var(--cyan)" stroke-width="1.6" fill="none"/></svg>
  <div class="quote-photo" role="img" aria-label="Portrait of Marisa T. Owner" style="left:242px;top:1960px;width:60px;height:64px"></div>
  <span class="dot" style="left:66px;top:1965px;width:3px;height:3px;background:var(--cyan)"></span>
  <span class="dot" style="left:474px;top:1988px;width:5px;height:5px;background:var(--orange)"></span>
  <span class="dot" style="left:175px;top:2043px;width:5px;height:5px;background:var(--orange)"></span>
  <span class="dot" style="left:410px;top:2037px;width:3px;height:3px;background:var(--violet)"></span>
  <span class="dot" style="left:128px;top:2151px;width:3px;height:3px;background:var(--navy)"></span>
  <p class="abs" style="left:0;right:0;top:2030px;text-align:center;font-size:8.5px;font-weight:500">Marisa T. Owner</p>
  <p class="abs" style="left:0;right:0;top:2043px;text-align:center;font-size:5px;color:var(--muted)">Summit Home Works</p>
  <div class="stars" style="top:2054px">★★★★★</div>
  <div class="circle-arrow" style="left:30px;top:2054px">←</div>
  <div class="circle-arrow" style="left:480px;top:2054px">→</div>
  <p class="quote" style="left:110px;width:325px;top:2082px">When it became apparent that a project would take more time than I had, Lena stepped up to take on the required research. She was thorough and timely; able to meet a last-minute 12-hour deadline. I would highly recommend Lena to assist with your next project.</p>

  <footer class="footer" style="height:240px;background:transparent">
    <svg class="abs" style="left:0;top:0" width="543" height="240" viewBox="0 0 543 240"><path d="M0 30 C150 -5 300 8 420 20 C480 26 515 18 543 12 L543 240 L0 240Z" fill="var(--black)"/></svg>
    <div class="abs" style="left:30px;top:66px;width:125px">
      <div class="brand" style="font-size:6.5px;color:#fff"><span class="brand-mark"></span>Lena Morvath</div>
      <p style="font-size:4.8px;line-height:8px;color:#cfcfd6;margin:12px 0 22px">Sed ut perspiciatis unde omnis iste natus error sit voluptatem...</p>
      <div class="social"><span></span><span></span><span></span></div>
    </div>
    <div class="abs foot-col" style="left:193px;top:60px"><h4>QUICK LINKS</h4><ul><li>Home</li><li>About Lena</li><li>Services</li><li>Portfolio</li><li>Pricing</li><li>Contact Us</li></ul></div>
    <div class="abs foot-col" style="left:290px;top:60px"><h4>SERVICES</h4><ul><li>Corporate Solution</li><li>Call Center Solution</li><li>Cloud System Solution</li></ul></div>
    <div class="abs foot-col" style="left:396px;top:60px;width:125px"><h4>CONTACT US</h4>
      <div class="contact-row"><i><svg width="7" height="8" viewBox="0 0 7 8"><path d="M3.5 8 C1 5 0.5 4 0.5 3 A3 3 0 0 1 6.5 3 C6.5 4 6 5 3.5 8Z" fill="#fff"/></svg></i><span>14/2k Lorem ipsum dolar sit amet Glassglow 25kl USA</span></div>
      <div class="contact-row"><i><svg width="7" height="7" viewBox="0 0 7 7"><path d="M1 0.5 L2.5 0.5 L3 2 L2 2.8 C2.5 3.8 3.2 4.5 4.2 5 L5 4 L6.5 4.5 L6.5 6 C3.5 6 1 3.5 1 0.5Z" fill="#fff"/></svg></i><span>555.014.2288</span></div>
      <div class="contact-row"><i><svg width="8" height="6" viewBox="0 0 8 6"><rect x=".5" y=".5" width="7" height="5" fill="none" stroke="#fff"/><path d="M.5 .5 L4 3.5 L7.5 .5" fill="none" stroke="#fff"/></svg></i><span>hello@lenamorvath.test</span></div>
    </div>
    <p class="copyright" style="top:200px">COPYRIGHT © 2023 <b>LENA MORVATH</b> . ALL RIGHTS RESERVED.</p>
  </footer>
</section>

</body>
</html>
```